Business Cards for new orthopaedic surgery practice

My husband and I are starting our own orthopaedic surgery practice. We are looking for a business card that is uniform, but one will have my name/title and the other will have his. You can just create one design with my name on it for now. But when I choose your design as the winning design I will ask that you add another copy with his name/title.

We are looking for classy, simple, elite all in one. We like dark blues/a little gold/yellow. Something that goes with our logo. We want our logo incorporated. Here is all the info you need:
Business name: RV Bone & Vitality Center
Location: 38517 North Willowmere Ave
Brightwater Falls, FL 33418
Phone: 954-218-4063
Fax: 954-582-7341
Email: info@myrvbonecare.example

Names: Lydia Vance, M.D.
Board Certified Hand and Upper Extremity Surgeon

Ebo Dansu, M.D.
Board Certified Hip & Knee Replacement/General Orthopaedic Surgeon

Can decide what you want to put on the back. Maybe a slogan:
Steady Hands. Lasting Strength

I am just going to upload our logo. The only thing is if we select you as the winning design, the location, and phone numbers may change. We will need your help to update that once fully solidified.

Industry/Entity Type

Medical

Contact Information for Business Card

Colors
0054AA
0677BA
7BADD7
CADEEF
E8F1F8
0094D4
00A9DD
6FCCEA
C7EBF8
E9F6FB

Requirements
Must have
• class, appeal,
Should not have
• We want to air on the side of masculine if we are looking at masculine vs. feminine feel. But we still want it classy, sophisticated, and something we will love

```html
<!DOCTYPE html>
<html lang="en">
<head>
<meta charset="utf-8">
<title>RV Bone &amp; Vitality Center – Business Card</title>
<link rel="stylesheet" href="https://fonts.googleapis.com/css2?family=Libre+Baskerville:wght@400;700&family=Arimo:wght@400&display=swap">
<style>
  :root {
    --page-bg: #e4e4e4;
    --navy-top: #2b3c66;
    --navy-bottom: #1b2750;
    --navy-ink: #1f2d5a;
    --navy-relief: #34487a;
    --gold: #c9a25e;
    --white: #ffffff;
    --text-light: #f2f4f8;
  }
  * { box-sizing: border-box; margin: 0; padding: 0; }
  html, body { width: 1200px; height: 1200px; overflow: hidden; }
  body { background: var(--page-bg); position: relative; font-family: "Arimo", Arial, sans-serif; }

  .card {
    position: absolute;
    width: 688px;
    height: 393px;
    overflow: hidden;
  }
  .card--front { left: 266px; top: 158px; background: var(--white); }
  .card--back {
    left: 262px; top: 653px;
    background: linear-gradient(180deg, var(--navy-top), var(--navy-bottom));
  }

  /* front: brand side */
  .brand-side {
    position: absolute; left: 0; top: 0; width: 347px; height: 100%;
    display: flex; align-items: center; justify-content: center;
  }
  .brand-ring {
    width: 236px; height: 236px; border-radius: 50%;
    border: 2px solid var(--gold);
    display: flex; align-items: center; justify-content: center;
    text-align: center;
  }
  .brand-name {
    font-family: "Libre Baskerville", Georgia, serif;
    font-weight: 700; color: var(--navy-ink);
    font-size: 21px; line-height: 1.35; letter-spacing: 1px;
    text-transform: uppercase;
  }
  .gold-divider {
    position: absolute; left: 347px; top: 0; width: 8px; height: 100%;
    background: var(--gold);
  }

  /* front: contact side */
  .info-side {
    position: absolute; left: 355px; top: 0; right: 0; height: 100%;
    background: linear-gradient(180deg, var(--navy-top), var(--navy-bottom));
    padding: 84px 0 0 30px;
    color: var(--text-light);
  }
  .person-name {
    font-family: "Libre Baskerville", Georgia, serif;
    font-weight: 700; color: var(--gold);
    font-size: 22px; letter-spacing: 0.5px; text-transform: uppercase;
  }
  .person-title { font-size: 15px; line-height: 19px; margin-top: 3px; }
  .address { font-size: 16px; line-height: 21px; margin-top: 17px; }
  .contact-list { list-style: none; margin-top: 12px; }
  .contact-list li {
    display: flex; align-items: center; gap: 12px;
    font-size: 16px; line-height: 20.5px;
  }
  .contact-icon { width: 15px; height: 15px; flex: none; fill: var(--gold); }

  /* back */
  .back-mark {
    position: absolute; left: 0; right: 0; top: 124px;
    text-align: center;
    font-family: "Libre Baskerville", Georgia, serif;
    font-weight: 700; color: var(--navy-relief);
    font-size: 42px; line-height: 1.2; letter-spacing: 2px;
    text-transform: uppercase;
  }
  .slogan {
    position: absolute; left: 0; right: 0; top: 336px;
    text-align: center; color: var(--gold);
    font-size: 16px; letter-spacing: 3.2px; text-transform: uppercase;
  }
</style>
</head>
<body>

<section class="card card--front">
  <div class="brand-side">
    <div class="brand-ring">
      <p class="brand-name">RV Bone &amp;<br>Vitality<br>Center</p>
    </div>
  </div>
  <div class="gold-divider"></div>
  <div class="info-side">
    <h1 class="person-name">Lydia Vance, M.D.</h1>
    <p class="person-title">Board Certified Hand and<br>Upper Extremity Surgeon</p>
    <p class="address">38517 North Willowmere Ave<br>Brightwater Falls, FL 33418</p>
    <ul class="contact-list">
      <li>
        <svg class="contact-icon" viewBox="0 0 16 16" aria-hidden="true"><path d="M3.5 1 6 3.8 4.7 5.6c.9 2 3.7 4.8 5.7 5.7L12.2 10 15 12.5 13.4 15C7 14.6 1.4 9 1 2.6Z"/></svg>
        <span>954-218-4063</span>
      </li>
      <li>
        <svg class="contact-icon" viewBox="0 0 16 16" aria-hidden="true"><rect x="4" y="1" width="8" height="5"/><rect x="1" y="7" width="14" height="6" rx="1"/><rect x="4" y="13" width="8" height="2"/></svg>
        <span>954-582-7341</span>
      </li>
      <li>
        <svg class="contact-icon" viewBox="0 0 16 16" aria-hidden="true"><path d="M1 4h14v1L8 9.5 1 5Z"/><path d="M1 6.3 8 10.8l7-4.5V13H1Z"/></svg>
        <span>info@myrvbonecare.example</span>
      </li>
      <li>
        <svg class="contact-icon" viewBox="0 0 16 16" aria-hidden="true"><circle cx="8" cy="8" r="7"/><path d="M5 4c2 0 2 2 4 2s1 3-1 3-1 3-3 3c0-2-2-2-2-4s2-2 2-4Z" fill="#24345f"/></svg>
        <span>www.myrvbonecare.example</span>
      </li>
    </ul>
  </div>
</section>

<section class="card card--back">
  <p class="back-mark">RV Bone &amp;<br>Vitality Center</p>
  <p class="slogan">Steady Hands. Lasting Strength</p>
</section>

</body>
</html>
```